Business Card Design (NEW FILES)

ATTENTION: New vector files are available. Please update your design to reflect/use the new (better resolution) logo images.

Seeking a unique and professional business card design for a commercial drone photography/videography business. The layout should feature
the logo (attached) and include the following information:
Owen Tarrick
614-502-7738
www.skylarkreelworks.example
NRD Certified Remote Pilot

Owen Tarrick

```html
<!DOCTYPE html>
<html lang="en">
<head>
<meta charset="utf-8">
<title>Skylark Reelworks – Business Card</title>
<link href="https://fonts.googleapis.com/css2?family=Open+Sans:wght@400;600;700&display=swap" rel="stylesheet">
<style>
  :root {
    --navy: #141a45;
    --orange: #eb8a4b;
    --white: #ffffff;
    --ink: #141a45;
    --stage: #222222;
  }
  * { box-sizing: border-box; margin: 0; padding: 0; }
  html, body { width: 1200px; height: 780px; overflow: hidden; background: var(--stage); }
  body { font-family: "Open Sans", Arial, sans-serif; display: flex; align-items: center; justify-content: center; gap: 60px; }

  .card { position: relative; width: 525px; height: 300px; border-radius: 20px; overflow: hidden; flex: none; }

  /* Front */
  .card-front { background: var(--white); }
  .brand-name { position: absolute; left: 30px; top: 58px; display: flex; align-items: center; gap: 8px;
    font-weight: 600; font-size: 20px; line-height: 1; color: var(--navy); white-space: nowrap; }
  .brand-dot { width: 12px; height: 12px; border-radius: 50%; background: var(--orange); flex: none; }
  .divider { position: absolute; left: 0; top: 0; }
  .contact { position: absolute; left: 300px; top: 92px; color: var(--ink); white-space: nowrap; }
  .contact-name { font-weight: 700; font-size: 26px; line-height: 1.1; }
  .contact-name .first { color: var(--orange); }
  .contact-role { font-size: 13px; font-weight: 600; line-height: 1.3; margin-bottom: 10px; }
  .contact-line { display: flex; align-items: center; gap: 7px; font-size: 12.5px; line-height: 1.6; }
  .contact-line svg { flex: none; }

  .footer-band { position: absolute; left: 0; bottom: 0; width: 100%; height: 36px; background: var(--navy);
    color: var(--white); font-size: 13px; padding-left: 28px; display: flex; align-items: center; }
  .footer-accent { position: absolute; right: 0; bottom: 0; width: 95px; height: 36px; background: var(--orange); }
  .drone-art { position: absolute; right: 30px; bottom: 22px; width: 120px; height: 44px; border-radius: 22px;
    background: linear-gradient(90deg, var(--navy), #3b4170); }

  /* Back */
  .card-back { background: var(--navy); display: flex; align-items: center; justify-content: center; }
  .back-brand { display: flex; align-items: center; gap: 14px; font-weight: 600; font-size: 34px; color: var(--white); white-space: nowrap; }
  .back-brand .brand-dot { width: 18px; height: 18px; }
</style>
</head>
<body>
  <section class="card card-front">
    <div class="brand-name"><span class="brand-dot"></span>Skylark Reelworks</div>
    <svg class="divider" width="525" height="300" viewBox="0 0 525 300" aria-hidden="true">
      <line x1="278" y1="96" x2="212" y2="212" stroke="#eb8a4b" stroke-width="1"/>
    </svg>
    <div class="contact">
      <p class="contact-name"><span class="first">Owen</span> Tarrick</p>
      <p class="contact-role">Owner</p>
      <p class="contact-line">
        <svg width="12" height="12" viewBox="0 0 24 24" aria-hidden="true"><path fill="#eb8a4b" d="M6.6 10.8a15 15 0 0 0 6.6 6.6l2.2-2.2c.3-.3.7-.4 1-.2 1.1.4 2.3.6 3.6.6.6 0 1 .4 1 1V20c0 .6-.4 1-1 1A17 17 0 0 1 3 4c0-.6.4-1 1-1h3.5c.6 0 1 .4 1 1 0 1.3.2 2.5.6 3.6.1.3 0 .7-.2 1z"/></svg>
        614-502-7738
      </p>
      <p class="contact-line">
        <svg width="12" height="12" viewBox="0 0 24 24" aria-hidden="true"><circle cx="12" cy="12" r="10" fill="none" stroke="#eb8a4b" stroke-width="2.5"/><path d="M2 12h20M12 2c3 3 3 17 0 20M12 2c-3 3-3 17 0 20" fill="none" stroke="#eb8a4b" stroke-width="2"/></svg>
        www.skylarkreelworks.example
      </p>
      <p class="contact-line">
        <svg width="12" height="12" viewBox="0 0 24 24" aria-hidden="true"><rect x="2" y="5" width="20" height="14" rx="2" fill="#eb8a4b"/><path d="M3 6l9 7 9-7" fill="none" stroke="#fff" stroke-width="2"/></svg>
        info@skylarkreelworks.example
      </p>
    </div>
    <div class="footer-band">NRD Certified Remote Pilot, Fully Insured</div>
    <div class="footer-accent"></div>
    <div class="drone-art" role="img" aria-label="Illustration of a camera drone in flight"></div>
  </section>

  <section class="card card-back">
    <div class="back-brand"><span class="brand-dot"></span>Skylark Reelworks</div>
  </section>
</body>
</html>
```